Timber Crest Construction Needs business card

Hey we are in need of business card designs. I have upload our logo as a guideline, but free feel to run with it or come up with something unique.
Pls have fun with it and be creative. the name says it all!
i will give some directions after i see a few entries..
Updates
Logo source file has been uploaded..
Hey because of the logo is so colourful already.
Can we have a few submissions with less colour.
Also we are looking for clever/hidden/descriptive business card.

```html
<!DOCTYPE html>
<html lang="en">
<head>
<meta charset="utf-8">
<title>Timber Crest Construction – Business Card</title>
<link href="https://fonts.googleapis.com/css2?family=Exo+2:wght@400;600;700&display=swap" rel="stylesheet">
<style>
  :root {
    --brand-blue: #1e8ed6;
    --brand-blue-dark: #1778bb;
    --slate: #8c8c8c;
    --slate-dark: #6f6f6f;
    --paper: #ffffff;
    --paper-shade: #eeeeee;
    --ink: #7a7a7a;
    --stage: #e4e6e9;
  }
  * { margin: 0; padding: 0; box-sizing: border-box; }
  html, body { width: 1200px; height: 863px; overflow: hidden; }
  body {
    background: var(--stage);
    font-family: "Exo 2", sans-serif;
    position: relative;
  }
  .card {
    position: absolute;
    left: 260px;
    width: 680px;
    height: 388px;
    box-shadow: 0 6px 18px rgba(0,0,0,.18);
  }
  .card--back { top: 28px; }
  .card--front { top: 447px; }
  .card svg { display: block; width: 680px; height: 388px; }
  .t-site { font: 600 20px "Exo 2", sans-serif; fill: var(--paper); letter-spacing: .5px; }
  .t-name { font: 700 32px "Exo 2", sans-serif; fill: var(--paper); letter-spacing: 1px; }
  .t-role { font: 400 14px "Exo 2", sans-serif; fill: var(--paper); letter-spacing: 1.5px; }
  .t-address { font: 600 19px "Exo 2", sans-serif; fill: var(--paper); letter-spacing: .5px; }
  .t-contact { font: 400 13px "Exo 2", sans-serif; fill: var(--paper); }
  .t-brand { font: 700 40px "Exo 2", sans-serif; fill: var(--ink); letter-spacing: .5px; }
  .t-brand-sub { font: 700 14px "Exo 2", sans-serif; fill: var(--ink); letter-spacing: 3px; }
  .t-brand-back { font: 700 26px "Exo 2", sans-serif; fill: var(--ink); }
  .icon { fill: var(--paper); }
</style>
</head>
<body>

  <!-- Back of card -->
  <div class="card card--back">
    <svg viewBox="0 0 680 388" aria-label="Card back">
      <rect class="back-field" width="680" height="388" fill="var(--brand-blue)"/>
      <path class="back-panel-shadow" d="M40 82 H330 Q352 82 360 104 L420 300 H40 Z" fill="var(--brand-blue-dark)" opacity=".35"/>
      <path class="back-panel" d="M0 70 H320 Q342 70 350 92 L408 290 H0 Z" fill="var(--paper-shade)"/>
      <rect class="brand-square" x="56" y="160" width="22" height="22" fill="var(--brand-blue)"/>
      <text class="t-brand-back" x="90" y="180">TIMBER CREST</text>
      <text class="t-brand-sub" x="90" y="204">CONSTRUCTION</text>
      <text class="t-site" x="640" y="110" text-anchor="end">www.timbercrestbuild.com</text>
    </svg>
  </div>

  <!-- Front of card -->
  <div class="card card--front">
    <svg viewBox="0 0 680 388" aria-label="Card front">
      <rect class="front-field" width="680" height="388" fill="var(--paper)"/>

      <path class="name-tab-shadow" d="M330 52 H680 V175 H430 Z" fill="var(--paper-shade)"/>
      <path class="name-tab" d="M372 30 H680 V160 H470 Q452 160 440 146 L362 52 Q356 30 372 30 Z" fill="var(--slate)"/>
      <text class="t-name" x="640" y="88" text-anchor="end">DANIEL REYES</text>
      <text class="t-role" x="640" y="114" text-anchor="end">GENERAL MANAGER</text>

      <path class="contact-band" d="M0 292 H300 L680 150 V388 H0 Z" fill="var(--brand-blue)"/>

      <rect class="brand-square" x="40" y="184" width="24" height="24" fill="var(--brand-blue)"/>
      <text class="t-brand" x="74" y="208">TIMBER CREST</text>
      <text class="t-brand-sub" x="76" y="232">CONSTRUCTION</text>

      <text class="t-address" x="640" y="272" text-anchor="end">42 Harlow Lane,</text>
      <text class="t-address" x="640" y="298" text-anchor="end">Unit 3 Westfield Park</text>

      <g class="contact-list">
        <path class="icon" d="M30 305 q2 -2 4 0 l2 3 q1 2 -1 3 q1 3 4 4 q1 -2 3 -1 l3 2 q2 2 0 4 q-3 3 -8 0 q-6 -4 -8 -9 q-1 -4 1 -6 z"/>
        <text class="t-contact" x="52" y="316">014 552 7380</text>

        <rect class="icon" x="32" y="325" width="8" height="13" rx="1.5"/>
        <text class="t-contact" x="52" y="336">014 552 7380</text>

        <rect class="icon" x="30" y="346" width="12" height="9" rx="1"/>
        <path d="M30 347 l6 5 l6 -5" stroke="var(--brand-blue)" stroke-width="1.2" fill="none"/>
        <text class="t-contact" x="52" y="355">daniel@timbercrestbuild.com</text>

        <circle cx="36" cy="370" r="6" fill="none" stroke="var(--paper)" stroke-width="1.5"/>
        <path d="M30 370 H42 M36 364 V376" stroke="var(--paper)" stroke-width="1.2"/>
        <text class="t-contact" x="52" y="375">www.timbercrestbuild.com</text>
      </g>
    </svg>
  </div>

</body>
</html>
```